Create a modern, visually appealing flyer for Courier Service.

Copperfinch Freight Flyer Design Brief

Project Overview
Create a modern, visually appealing, front-and-back 8.5"x11" flyer for Copperfinch Freight to distribute to potential customers and vendors. The flyer should emphasize the company's expansive service area, reliability, technological capabilities, and broad service offerings.

Flyer Goals
Showcase Copperfinch's extensive regional coverage
Highlight core services, industries served, technology integration, certifications, and fleet capabilities
Convey reliability, modernity, and technology-driven professionalism
Encourage further interaction via a QR code (to be placed later by Copperfinch)

Visual Style & Branding
Color Scheme: Creative, modern colors that are vibrant and appealing, suitable for a technology-driven and professional logistics company.
Font Selection: Modern, clean, professional fonts; readability is essential. Update to Logo
Design Aesthetic: Balanced mix of minimalistic/clean, tech-driven/futuristic, and sophisticated/professional elements.
Background: Incorporate abstract graphic patterns or imagery reflecting logistics, technology, or mapping concepts (e.g., subtle maps, abstract roads).

Content Layout

Front Side

Company Name & Logo: Prominent but balanced

Service Area Map: Modern, stylized graphic highlighting North Dakota, Minnesota, Montana, South Dakota, and Northern Iowa, clearly marking major cities within these areas

Vehicle Graphic: Stylized graphic featuring a Halvek Porta van with the Copperfinch logo clearly visible

Certifications (as official logo badges): HIPAA, Hazmat/DOT, Radiopharmaceutical, TSA/IAC

Contact Information:

Copperfinch Freight, LLC

2964 41st Ave S, Suite 315, Fargo, ND 58104

www.cprfinch-example.com | dispatch@cprfinch-example.com

Back Side

Core Services (icons, modern style):

STAT/ASAP

Same Day

Next Day

Scheduled

Extended Drives

Onboard Courier / Hand Carry

Reverse Logistics

White Glove

Warehousing

Industries Served (icons matching services style):

Healthcare & Life Sciences

Pharmaceuticals

Retailers & E-Commerce

Distributors & Manufacturers

Educational Institutions

Legal & Financial Services

Food & Beverage

Technology & IT Companies

Government & Defense Companies

Technology Highlights:

Advanced Integration Capabilities

GPS Tracking

Live Vehicle Monitoring

Client Online Portal

Emphasis on Real-Time Tracking and seamless integrations

Fleet Capabilities:

Variety of Vehicles: Sedans, SUVs, Pickup Trucks, Cargo Vans, Sprinters, Straight Trucks

Key Vehicle Features: Liftgate capabilities prominently noted

Hub Locations: Clearly listed:

Fargo, ND

Bismarck, ND

Devils Lake, ND

Grand Forks, ND

Airport Codes Serviced:

FAR - Fargo, ND

BIS - Bismarck, ND

MOT - Minot, ND

GFK - Grand Forks, ND

XWA - Williston, ND

DIK - Dickinson, ND

DVL - Devils Lake, ND

JMS - Jamestown, ND

ABR - Aberdeen, SD

ATY - Watertown, SD

TRF - Thief River Falls, MN

BJI - Bemidji, MN

DTL - Detroit Lakes, MN

MSP - Minneapolis/St. Paul, MN

Design Elements

Use of modern graphics and custom icons for services and industries

Abstract patterns or technology-driven imagery

Professional but approachable tone, using concise, bulleted text organized clearly in sections

Avoid event-specific language; design for long-term general use

Imagery

Stylized, consistent iconography for services and industries

Stylized vehicle graphics (Halvek Porta van)

Custom graphics illustrating technology integrations (if official graphics unavailable)

Images from software provider's website: www.QuillbyteApps.com

Technical Requirements

8.5” x 11” flyer, double-sided

Digital-ready files provided for printing in-house; no specific print preferences necessary

High-resolution files suitable for both print and digital use

Deliverables

Editable source files (Adobe Illustrator, Photoshop, or InDesign)

High-resolution PDF for printing

Web-friendly PDF or digital version

This flyer should clearly communicate Copperfinch Freight’ commitment to reliable, technology-enhanced logistics solutions across the region, effectively engaging diverse audiences across key industries.

Concept 1: Modern Technology Hub
Front:
Dominated by an abstract, vibrant map illustrating the service region with key cities pinpointed.
The Copperfinch logo prominently at the top left, with stylized Halvek Porta van graphic subtly integrated onto the map roads.
Certifications as bold, minimalistic badges along the lower edge.
Crisp, clear contact info at bottom-right.
Back:
Split vertically into distinct sections, each clearly labeled with modern iconography for:
Core Services
Industries Served
Technology Highlights (with Quillbyte Apps visuals)
Fleet Capabilities (vehicle silhouettes/icons)
Airport codes listed in a streamlined table format along the bottom.
Abstract tech-pattern background (faded nodes, routes, or circuit-board style).

Concept 2: Futuristic Minimalism
Front:
Sleek, minimalist layout with a clean white or very light background.
Modern service area map using minimalist outlines and dots for major cities, in gradient blues or tech-inspired palette.
Prominent Copperfinch Freight logo at top-center.
Stylized Halvek Porta graphic appearing subtly at bottom corner.
Certifications displayed vertically as sleek, simplified logo badges.
Back:
Horizontally segmented sections for:
Core Services with clean, futuristic icons.
Industries Served section with matching sleek icons.
Technology Highlights, centered around Quillbyte Apps graphics and abstract integrated circuit imagery.
Fleet Capabilities detailed with simplified vehicle graphics.
Clearly defined hub locations and airport codes in a clean, structured list along the side.

Concept 3: Bold & Vibrant Professionalism
Front:
Bright, vivid color blocking with abstract geometric shapes referencing routes and logistics paths.
The service map as a central graphic, bold and modern, clearly marking key hubs.
A prominent stylized Halvek Porta van with Copperfinch logo creatively placed along the lower third of the flyer.
Certifications featured prominently within colored circular badges along the top or side.
Contact details neatly integrated at the bottom.
Back:
Dynamic grid layout clearly displaying:
Core Services and Industries Served with bold, vibrant icons.
Technology Highlights, clearly emphasized with screenshots or custom graphics from Quillbyte Apps.
Fleet Capabilities section featuring colorful vehicle silhouettes/icons.
Hub locations and airport codes clearly called out within visually appealing graphics or charts.
Rich abstract graphical background elements maintaining professional readability.

Designers should not use AI for designs.

Target Market(s)

Businesses Needing Courier Services

Font styles to use
Sans Serif

```html
<!DOCTYPE html>
<html lang="en">
<head>
<meta charset="utf-8">
<title>Copperfinch Freight, LLC — Flyer</title>
<link rel="stylesheet" href="https://fonts.googleapis.com/css2?family=Montserrat:wght@400;500;600;700;800&family=Poppins:wght@300;400;500;600;700&display=swap">
<style>
:root{
  --tan:#b8937a;
  --tan-light:#efe6de;
  --brown:#4a2c1d;
  --brown-mid:#6b4430;
  --accent:#b08a6c;
  --yellow:#f3ec78;
  --hub:#dcd68e;
  --ink:#111111;
  --white:#ffffff;
  --paper:#ffffff;
  --nd:#f3ec78;
  --mn:#5dbb2f;
  --mt:#7fa8f3;
  --sd:#1d5a9c;
  --ia:#e0761a;
}
*{box-sizing:border-box;margin:0;padding:0}
html,body{width:1200px;height:3089px;overflow:hidden;background:var(--paper)}
body{position:relative;font-family:"Poppins",sans-serif;color:var(--ink)}
.page{position:absolute;box-shadow:0 18px 40px rgba(0,0,0,.18);overflow:hidden}
.abs{position:absolute}

/* ---------- front ---------- */
.front{left:102px;top:144px;width:996px;height:1290px;
  background:radial-gradient(ellipse 60% 55% at 50% 48%,var(--tan-light) 0%,#d8c3b2 45%,var(--tan) 100%)}
.brand{left:0;width:100%;top:66px;display:flex;justify-content:center;align-items:center;gap:16px}
.brand-dot{width:44px;height:44px;border-radius:50%;background:var(--brown)}
.brand-name{font-family:"Montserrat",sans-serif;font-weight:800;font-size:34px;line-height:1;color:var(--brown);letter-spacing:-.5px}
.brand-tag{left:0;width:100%;top:152px;text-align:center;font-size:14px;letter-spacing:2.5px;color:var(--brown)}
.hero-title{left:0;width:100%;top:210px;text-align:center;font-family:"Montserrat",sans-serif;line-height:.9}
.hero-title .l1{display:block;font-weight:800;font-size:108px;color:var(--ink);letter-spacing:-2px}
.hero-title .l2{display:block;font-weight:500;font-size:100px;color:var(--white);letter-spacing:-2px}
.area-map{left:90px;top:468px;width:594px;height:258px;border-radius:30px 60px 20px 40px;
  background:linear-gradient(120deg,#ececec 0%,#dcdcdc 45%,#cfd6c8 100%);opacity:.95}
.legend{left:709px;top:494px}
.legend h3{font-family:"Montserrat",sans-serif;font-weight:800;font-size:22px;line-height:.9;color:var(--ink)}
.legend h3 span{color:var(--brown-mid)}
.legend ul{list-style:none;margin-top:22px}
.legend li{display:flex;align-items:center;gap:10px;height:34px;font-family:"Montserrat",sans-serif;font-weight:600;font-size:15px;color:var(--ink)}
.legend i{width:22px;height:22px;border-radius:50%;display:block}
.van{left:78px;top:726px;width:780px;height:400px;border-radius:70px 110px 30px 40px;
  background:linear-gradient(180deg,#cfcfcf 0%,#e9e9e9 30%,#ece68f 55%,#d9d07a 75%,#a98f74 100%)}
.front-foot{left:0;top:1180px;width:100%;height:80px}
.foot-name{left:76px;top:8px;font-family:"Montserrat",sans-serif;font-weight:800;font-size:22px;line-height:1.2;color:var(--white)}
.foot-addr{left:310px;top:4px;font-weight:300;font-size:19px;line-height:1.25;color:var(--white);display:flex;gap:14px}
.foot-web{left:614px;top:0;font-weight:300;font-size:23px;line-height:1.25;color:var(--white)}
.foot-web div,.back-foot .web div{display:flex;align-items:center;gap:12px}
.ico{flex:none}

/* ---------- back ---------- */
.back{left:100px;top:1656px;width:1002px;height:1296px;background:var(--paper)}
.services-band{left:0;top:0;width:100%;height:316px;background:var(--tan)}
.services-band h2{position:absolute;left:80px;top:56px;font-family:"Montserrat",sans-serif;font-weight:800;font-size:36px;color:var(--white);letter-spacing:1px}
.svc{display:flex;align-items:center;gap:14px;font-size:17px;color:var(--white)}
.svc-ico{width:48px;height:48px;border-radius:50%;background:var(--brown);display:flex;align-items:center;justify-content:center;flex:none}
.tech h2{position:absolute;left:80px;top:348px;font-family:"Montserrat",sans-serif;font-weight:700;font-size:25px}
.tech-item{left:78px;width:500px;display:flex;gap:12px}
.tech-ico{width:48px;height:48px;border-radius:50%;background:var(--ink);flex:none;display:flex;align-items:center;justify-content:center}
.tech-item h3{font-family:"Montserrat",sans-serif;font-weight:700;font-size:20px;line-height:1.2;color:var(--accent)}
.tech-item p{font-size:14.5px;line-height:1.25;color:var(--ink);margin-top:10px}
.ind-tab{left:623px;top:340px;width:264px;height:42px;background:var(--brown);border-radius:8px;color:var(--white);font-family:"Montserrat",sans-serif;font-weight:700;font-size:24px;text-align:center;line-height:42px;z-index:2}
.ind-box{left:590px;top:380px;width:332px;height:472px;border:1.5px solid #555;border-radius:12px}
.ind-box ul{list-style:none;position:absolute;left:28px;top:42px}
.ind-box li{display:flex;align-items:center;gap:10px;height:46px;font-size:18px;color:var(--ink)}
.fleet{left:79px;top:876px;width:461px;height:190px;background:var(--tan);border-radius:14px}
.fleet h3{position:absolute;left:26px;top:14px;font-family:"Montserrat",sans-serif;font-weight:800;font-size:25px;color:var(--white)}
.fleet h4{position:absolute;left:26px;top:52px;font-family:"Montserrat",sans-serif;font-weight:800;font-size:20px;color:var(--ink)}
.fleet ul{list-style:none;position:absolute;left:26px;top:82px;font-size:15px;line-height:18px;color:var(--white)}
.fleet-van{left:186px;top:40px;width:262px;height:140px;border-radius:30px 50px 14px 20px;
  background:linear-gradient(180deg,#cfcfcf 0%,#e9e9e9 35%,#ece68f 60%,#a98f74 100%)}
.feature{left:79px;top:1075px;width:461px;height:77px;background:var(--tan);border-radius:14px}
.feature h3{position:absolute;left:26px;top:12px;font-family:"Montserrat",sans-serif;font-weight:800;font-size:20px;color:var(--ink)}
.feature p{position:absolute;left:26px;top:44px;font-size:15px;color:var(--white)}
.hubs{left:589px;top:876px;width:331px;height:108px;background:var(--hub);border-radius:12px}
.hubs h3{position:absolute;left:20px;top:14px;font-family:"Montserrat",sans-serif;font-weight:800;font-size:20px;color:var(--brown)}
.hubs .grid{position:absolute;left:20px;top:52px;display:grid;grid-template-columns:170px 140px;row-gap:6px;font-size:15px;color:#6b5a3c}
.airports h3{position:absolute;left:601px;top:1018px;font-family:"Montserrat",sans-serif;font-weight:800;font-size:26px;color:var(--brown-mid)}
.airports .grid{position:absolute;left:601px;top:1060px;display:grid;grid-template-columns:168px 140px;row-gap:8px;font-family:"Montserrat",sans-serif;font-weight:500;font-size:14px}
.back-foot{left:0;top:1130px;width:100%;height:166px}
.back-foot svg.band{position:absolute;left:0;top:0}
.back-foot .name{left:79px;top:50px;font-family:"Montserrat",sans-serif;font-weight:800;font-size:20px;line-height:1.2;color:var(--accent)}
.back-foot .rule{top:46px;width:1.5px;height:42px;background:var(--hub)}
.back-foot .addr{left:330px;top:46px;font-size:16px;line-height:1.25;color:var(--white);display:flex;gap:12px}
.back-foot .web{left:668px;top:42px;font-size:17px;line-height:1.45;color:var(--white)}
</style>
</head>
<body>

<section class="page front">
  <div class="abs brand"><span class="brand-dot"></span><span class="brand-name">Copperfinch Freight</span></div>
  <p class="abs brand-tag">Same Day &amp; Scheduled Deliveries</p>
  <h1 class="abs hero-title"><span class="l1">Copperfinch</span><span class="l2">Freight, LLC</span></h1>

  <div class="abs area-map" role="img" aria-label="Map of the United States highlighting Montana, North Dakota, South Dakota, Minnesota and northern Iowa with location pins"></div>

  <div class="abs legend">
    <h3>OUR SERVICE<br><span>AREA MAP</span></h3>
    <ul>
      <li><i style="background:var(--nd)"></i>NORTH DAKOTA</li>
      <li><i style="background:var(--mn)"></i>MINNESOTA</li>
      <li><i style="background:var(--mt)"></i>MONTANA</li>
      <li><i style="background:var(--sd)"></i>SOUTH DAKOTA</li>
      <li><i style="background:var(--ia)"></i>NORTHERN IOWA</li>
    </ul>
  </div>

  <div class="abs van" role="img" aria-label="Branded delivery van in grey, yellow and tan livery with company name and website"></div>

  <div class="abs front-foot">
    <div class="abs foot-name">COPPERFINCH<br>FREIGHT, LLC</div>
    <div class="abs foot-addr">
      <svg class="ico" width="18" height="22" viewBox="0 0 18 22"><path d="M9 1a7 7 0 0 0-7 7c0 5 7 13 7 13s7-8 7-13a7 7 0 0 0-7-7z" fill="#fff"/><circle cx="9" cy="8" r="2.6" fill="#b8937a"/></svg>
      <span>2964 41st Ave S, Suite 315<br>Fargo, ND 58104</span>
    </div>
    <div class="abs foot-web">
      <div><svg class="ico" width="16" height="16" viewBox="0 0 16 16"><circle cx="8" cy="8" r="7" fill="none" stroke="#fff" stroke-width="1.6"/><path d="M1 8h14M8 1c3 3 3 11 0 14M8 1c-3 3-3 11 0 14" fill="none" stroke="#fff" stroke-width="1.2"/></svg>www.cprfinch-example.com</div>
      <div><svg class="ico" width="16" height="16" viewBox="0 0 16 16"><circle cx="8" cy="8" r="8" fill="#fff"/><rect x="3.5" y="5" width="9" height="6" fill="none" stroke="#b8937a" stroke-width="1.2"/><path d="M3.5 5l4.5 3.5L12.5 5" fill="none" stroke="#b8937a" stroke-width="1.2"/></svg>dispatch@cprfinch-example.com</div>
    </div>
  </div>
</section>

<section class="page back">
  <div class="abs services-band">
    <h2>CORE&nbsp; SERVICES</h2>
    <div class="abs svc" style="left:80px;top:116px"><span class="svc-ico"><svg width="24" height="22" viewBox="0 0 24 22"><path d="M3 20V14M8 20V10M13 20V7M18 20V4" stroke="#fff" stroke-width="3"/><path d="M2 9l8-5 4 3 8-6" stroke="#fff" stroke-width="1.5" fill="none"/></svg></span>STAT / ASAP</div>
    <div class="abs svc" style="left:80px;top:176px"><span class="svc-ico"><svg width="22" height="22" viewBox="0 0 22 22"><rect x="2" y="4" width="18" height="16" rx="2" fill="#fff"/><rect x="2" y="4" width="18" height="4" fill="#ddd"/><text x="11" y="18" font-size="9" text-anchor="middle" fill="#4a2c1d" font-family="Poppins">21</text></svg></span>Same Day</div>
    <div class="abs svc" style="left:80px;top:240px"><span class="svc-ico"><svg width="22" height="22" viewBox="0 0 22 22"><rect x="2" y="4" width="18" height="16" rx="2" fill="#fff"/><path d="M6 13h9M12 10l3 3-3 3" stroke="#4a2c1d" stroke-width="2" fill="none"/></svg></span>Next Day</div>
    <div class="abs svc" style="left:334px;top:124px"><span class="svc-ico"><svg width="22" height="22" viewBox="0 0 22 22"><rect x="2" y="4" width="18" height="16" rx="2" fill="#fff"/><path d="M5 11h3M10 11h3M15 11h2M5 15h3M10 15h3" stroke="#4a2c1d" stroke-width="2"/></svg></span>Scheduled</div>
    <div class="abs svc" style="left:334px;top:184px"><span class="svc-ico"><svg width="22" height="22" viewBox="0 0 22 22"><rect x="2" y="2" width="18" height="18" rx="2" fill="none" stroke="#fff" stroke-width="2"/><path d="M6 6l4 4M16 6l-4 4M6 16l4-4M16 16l-4-4" stroke="#fff" stroke-width="2"/></svg></span>Extended Drives</div>
    <div class="abs svc" style="left:334px;top:244px"><span class="svc-ico"><svg width="22" height="22" viewBox="0 0 22 22"><rect x="3" y="8" width="16" height="12" rx="2" fill="#fff"/><path d="M7 8V5a4 4 0 0 1 8 0v3" stroke="#fff" stroke-width="2" fill="none"/></svg></span>Onboard Courier / Hand Carry</div>
    <div class="abs svc" style="left:718px;top:124px"><span class="svc-ico"><svg width="24" height="24" viewBox="0 0 24 24"><path d="M19 12a7 7 0 1 1-3-5.7" stroke="#fff" stroke-width="2" fill="none"/><path d="M14 3l3 3-4 1" stroke="#fff" stroke-width="2" fill="none"/><rect x="9" y="10" width="6" height="5" fill="#fff"/></svg></span>Reverse Logistics</div>
    <div class="abs svc" style="left:718px;top:184px"><span class="svc-ico"><svg width="22" height="24" viewBox="0 0 22 24"><path d="M6 22V9M9 22V4M13 22V4M16 22V8M3 13l3 9h10" stroke="#fff" stroke-width="2.2" fill="none" stroke-linecap="round"/></svg></span>White Glove</div>
    <div class="abs svc" style="left:718px;top:248px"><span class="svc-ico"><svg width="24" height="22" viewBox="0 0 24 22"><path d="M2 8l10-6 10 6v12H2z" fill="#fff"/><rect x="6" y="11" width="12" height="9" fill="#4a2c1d"/><path d="M6 14h12M6 17h12" stroke="#fff" stroke-width="1"/></svg></span>Warehousing</div>
  </div>

  <div class="tech">
    <h2>Technology Highlights</h2>
    <div class="abs tech-item" style="top:400px"><span class="tech-ico"><svg width="26" height="26" viewBox="0 0 26 26"><circle cx="13" cy="13" r="9" fill="none" stroke="#fff" stroke-width="2" stroke-dasharray="3 2"/><circle cx="13" cy="13" r="4" fill="#fff"/></svg></span>
      <div><h3>Advanced Integration<br>Capabilities</h3><p>Easily connect with your existing systems<br>for streamlined operations. Our platform supports<br>robust API and EDI integrations tailored to your workflow.</p></div></div>
    <div class="abs tech-item" style="top:532px"><span class="tech-ico"><svg width="26" height="26" viewBox="0 0 26 26"><circle cx="11" cy="11" r="7" fill="none" stroke="#fff" stroke-width="2"/><path d="M16 16l6 6" stroke="#fff" stroke-width="2.5"/><path d="M11 6a4 4 0 0 0-4 4c0 3 4 6 4 6s4-3 4-6a4 4 0 0 0-4-4z" fill="#fff"/></svg></span>
      <div><h3>Real-Time GPS Tracking<br>&amp; Monitoring</h3><p style="margin-top:20px">Track every shipment live with pinpoint accuracy.<br>Enjoy full visibility into driver location, route, and<br>delivery status—updated in real time.</p></div></div>
    <div class="abs tech-item" style="top:666px"><span class="tech-ico"><svg width="26" height="26" viewBox="0 0 26 26"><circle cx="8" cy="8" r="3" fill="#fff"/><circle cx="18" cy="8" r="3" fill="#fff"/><path d="M3 17c2-3 8-3 10 0M13 17c2-3 8-3 10 0" stroke="#fff" stroke-width="2" fill="none"/><path d="M4 21h18" stroke="#fff" stroke-width="2"/></svg></span>
      <div><h3>Client Online Portal</h3><p style="margin-top:4px">Access orders, track deliveries, and manage<br>documents—all in one user-friendly dashboard.<br>Available 24/7 to keep you in control.</p></div></div>
    <div class="abs tech-item" style="top:770px"><span class="tech-ico"><svg width="26" height="26" viewBox="0 0 26 26"><circle cx="13" cy="13" r="9" fill="none" stroke="#fff" stroke-width="2"/><circle cx="9" cy="11" r="2" fill="#fff"/><circle cx="17" cy="11" r="2" fill="#fff"/><circle cx="13" cy="17" r="2" fill="#fff"/></svg></span>
      <div><h3>Seamless Tech Integrations</h3><p style="margin-top:4px">We work with your tools, not against them.<br>Our technology integrates effortlessly with CRMs,<br>ERPs, and shipping platforms for a unified experience.</p></div></div>
  </div>

  <div class="abs ind-tab">Industries Served</div>
  <div class="abs ind-box">
    <ul>
      <li><svg width="20" height="20" viewBox="0 0 20 20"><circle cx="10" cy="10" r="9" fill="#a85e3e"/><path d="M6 10l3 3 5-6" stroke="#fff" stroke-width="2" fill="none"/></svg>Healthcare &amp; Life Sciences</li>
      <li><svg width="20" height="20" viewBox="0 0 20 20"><circle cx="10" cy="10" r="9" fill="#a85e3e"/><path d="M6 10l3 3 5-6" stroke="#fff" stroke-width="2" fill="none"/></svg>Pharmaceuticals</li>
      <li><svg width="20" height="20" viewBox="0 0 20 20"><circle cx="10" cy="10" r="9" fill="#a85e3e"/><path d="M6 10l3 3 5-6" stroke="#fff" stroke-width="2" fill="none"/></svg>Retail &amp; E-Commerce</li>
      <li><svg width="20" height="20" viewBox="0 0 20 20"><circle cx="10" cy="10" r="9" fill="#a85e3e"/><path d="M6 10l3 3 5-6" stroke="#fff" stroke-width="2" fill="none"/></svg>Distributors &amp; Manufacturers</li>
      <li><svg width="20" height="20" viewBox="0 0 20 20"><circle cx="10" cy="10" r="9" fill="#a85e3e"/><path d="M6 10l3 3 5-6" stroke="#fff" stroke-width="2" fill="none"/></svg>Educational Institutions</li>
      <li><svg width="20" height="20" viewBox="0 0 20 20"><circle cx="10" cy="10" r="9" fill="#a85e3e"/><path d="M6 10l3 3 5-6" stroke="#fff" stroke-width="2" fill="none"/></svg>Legal &amp; Financial Services</li>
      <li><svg width="20" height="20" viewBox="0 0 20 20"><circle cx="10" cy="10" r="9" fill="#a85e3e"/><path d="M6 10l3 3 5-6" stroke="#fff" stroke-width="2" fill="none"/></svg>Food &amp; Beverage</li>
      <li><svg width="20" height="20" viewBox="0 0 20 20"><circle cx="10" cy="10" r="9" fill="#a85e3e"/><path d="M6 10l3 3 5-6" stroke="#fff" stroke-width="2" fill="none"/></svg>Technology &amp; IT</li>
      <li><svg width="20" height="20" viewBox="0 0 20 20"><circle cx="10" cy="10" r="9" fill="#a85e3e"/><path d="M6 10l3 3 5-6" stroke="#fff" stroke-width="2" fill="none"/></svg>Government &amp; Defense</li>
    </ul>
  </div>

  <div class="abs fleet">
    <h3>Fleet Capabilities</h3>
    <h4>Vehicle Types:</h4>
    <ul><li>Sedans</li><li>SUVs</li><li>Pickup Trucks</li><li>Cargo Vans</li><li>Sprinters</li><li>Straight Trucks</li></ul>
    <div class="abs fleet-van" role="img" aria-label="Branded delivery van in company livery"></div>
  </div>
  <div class="abs feature"><h3>Special Feature:</h3><p>Liftgate-equipped vehicles</p></div>

  <div class="abs hubs">
    <h3>Hub Locations</h3>
    <div class="grid"><span>Devils Lake, ND</span><span>Fargo, ND</span><span>Grand Forks, ND</span><span>Bismarck, ND</span></div>
  </div>
  <div class="airports">
    <h3>Airport Codes Serviced</h3>
    <div class="grid"><span>FAR • BIS • MOT</span><span>ATY • TRF • BJI</span><span>GFK • XWA • DIK</span><span>DTL • MSP</span><span>DVL • JMS • ABR</span><span></span></div>
  </div>

  <div class="abs back-foot">
    <svg class="band" width="1002" height="166" viewBox="0 0 1002 166"><polygon points="0,24 560,24 588,0 1002,0 1002,166 0,166" fill="#000"/></svg>
    <div class="abs name">COPPERFINCH<br>FREIGHT, LLC</div>
    <div class="abs rule" style="left:286px"></div>
    <div class="abs addr">
      <svg class="ico" width="16" height="20" viewBox="0 0 18 22"><path d="M9 1a7 7 0 0 0-7 7c0 5 7 13 7 13s7-8 7-13a7 7 0 0 0-7-7z" fill="#fff"/><circle cx="9" cy="8" r="2.6" fill="#000"/></svg>
      <span>2964 41st Ave S, Suite<br>315 Fargo, ND 58104</span>
    </div>
    <div class="abs rule" style="left:610px"></div>
    <div class="abs web">
      <div><svg class="ico" width="15" height="15" viewBox="0 0 16 16"><circle cx="8" cy="8" r="7" fill="none" stroke="#fff" stroke-width="1.6"/><path d="M1 8h14M8 1c3 3 3 11 0 14M8 1c-3 3-3 11 0 14" fill="none" stroke="#fff" stroke-width="1.2"/></svg>www.cprfinch-example.com</div>
      <div><svg class="ico" width="15" height="15" viewBox="0 0 16 16"><circle cx="8" cy="8" r="8" fill="#fff"/><rect x="3.5" y="5" width="9" height="6" fill="none" stroke="#000" stroke-width="1.2"/><path d="M3.5 5l4.5 3.5L12.5 5" fill="none" stroke="#000" stroke-width="1.2"/></svg>dispatch@cprfinch-example.com</div>
    </div>
  </div>
</section>

</body>
</html>
```